Waste management company seeks a new website design

We need a website design for an environmental services company called 'Laanemetsa Haldusgrupp.' We manage waste collection and recycling for 100K+ households and businesses across Estonia. Please use logos and colors from attached CVI file. The design should be extensively usable for our self-service portal and have a mobile-first approach as it will be turned into an app in the future. The new website should highlight our commitment to sustainability and provide easy access to our services with a clean, modern design. UX inspiration from https://ruvako.eu/et-ee/

```html
<!DOCTYPE html>
<html lang="en">
<head>
<meta charset="utf-8">
<title>Laanemetsa Haldusgrupp</title>
<link href="https://fonts.googleapis.com/css2?family=Poppins:wght@300;400;500;600;700&display=swap" rel="stylesheet">
<style>
:root{
  --lime:#cbd92a;
  --lime-dark:#b8c51f;
  --taupe:#8f8482;
  --ink:#2a2a2a;
  --text:#555;
  --muted:#8a8a8a;
  --footer:#2b2b2b;
  --white:#fff;
}
*{box-sizing:border-box;margin:0;padding:0}
html,body{width:1200px;height:3878px;overflow:hidden}
body{position:relative;font-family:"Poppins",sans-serif;color:var(--ink);background:var(--white)}
.abs{position:absolute}
.btn{position:absolute;display:flex;align-items:center;justify-content:center;border-radius:30px;background:var(--lime);color:var(--ink);font-weight:600;font-size:15px;text-decoration:none}
.brand{position:absolute;display:flex;align-items:center;gap:12px;font-size:21px;font-weight:500;color:var(--taupe);line-height:1.05}
.brand-dot{width:50px;height:50px;border-radius:50%;background:var(--lime);flex:none}
.section-title{position:absolute;display:flex;align-items:center;gap:12px;font-weight:700;font-size:34px;color:var(--ink)}
.section-title::before{content:"";width:26px;height:26px;border-radius:50%;background:var(--lime)}
.copy{position:absolute;font-size:14.5px;line-height:26.5px;color:var(--text);text-align:justify}

/* header */
.site-header{position:absolute;left:0;top:0;width:1200px;height:77px;background:rgba(255,255,255,.85);z-index:5}
.header-nav{position:absolute;top:16px;right:127px;display:flex;align-items:center;gap:30px;font-size:15px;font-weight:500}
.signup{background:var(--taupe);color:#fff;border-radius:24px;width:112px;height:46px;display:flex;align-items:center;justify-content:center;font-weight:600}
.menu{position:absolute;right:57px;top:28px;width:28px}
.menu span{display:block;height:3px;background:var(--ink);margin-bottom:6px;border-radius:2px}

/* hero */
.hero{position:absolute;left:0;top:0;width:1200px;height:760px;overflow:hidden}
.hero-photo{position:absolute;inset:0;background:linear-gradient(110deg,#5a4632 0%,#b38a5c 30%,#e0b58c 55%,#d79a63 75%,#8a6a3b 100%)}
.hero-welcome{left:578px;top:215px;font-size:37px;font-weight:400;color:#222}
.hero-title{left:576px;top:272px;font-size:52px;font-weight:700;line-height:62px;color:#222}

/* services */
.services{position:absolute;left:0;top:1335px;width:1200px;height:514px;background:linear-gradient(180deg,#9c9290 0%,#8e8785 45%,#8a8272 100%)}
.service-card{position:absolute;top:165px;width:310px;height:266px;background:#fff;border-radius:60px 0 0 0;text-align:center}
.service-card.active{background:var(--lime)}
.service-icon{width:94px;height:94px;border-radius:50%;background:var(--lime);border:6px solid #eef3a6;margin:20px auto 0;display:flex;align-items:center;justify-content:center}
.active .service-icon{background:#fff;border-color:#e6ee8e}
.service-card h3{font-size:18px;font-weight:600;margin-top:18px;color:var(--ink)}
.service-card p{font-size:12px;line-height:19.5px;color:var(--muted);margin:10px 32px 0}
.active p{color:#6f7420}
.circle-arrow{position:absolute;width:44px;height:44px;border-radius:50%;display:flex;align-items:center;justify-content:center}

/* reviews */
.reviews{position:absolute;left:0;top:2432px;width:1200px;height:590px;background:linear-gradient(180deg,#f1efee 0%,#ebe7e4 50%,#f3f1ef 100%)}
.review-card{position:absolute;top:164px;width:298px;height:348px;background:#fff;border-top:3px solid #ddd;border-radius:4px;padding:30px 26px;box-shadow:0 2px 10px rgba(0,0,0,.05)}
.review-card.active{border-top-color:var(--lime)}
.quote{font-size:40px;line-height:30px;color:#ccc;font-weight:700}
.stars{color:#f08a1c;font-size:16px;letter-spacing:2px;margin-top:12px}
.review-card p{font-size:14px;line-height:26.5px;color:#444;margin-top:16px}
.review-card hr{border:0;border-top:1px solid #e5e5e5;margin:26px 0 18px}
.review-card h4{font-size:17px;font-weight:600}
.review-card small{font-size:11px;color:#666}

/* news */
.news-item{position:absolute;top:3212px;width:317px}
.news-photo{height:180px}
.news-item h4{font-size:17.5px;font-weight:600;line-height:30px;margin:12px 6px 0}
.news-item time{display:block;font-size:11px;color:#777;margin:10px 4px 0}

/* footer */
.site-footer{position:absolute;left:0;top:3588px;width:1200px;height:290px;background:var(--footer);color:#e8e8e8}
.footer-col{position:absolute;top:77px;font-size:15px;line-height:25px}
.footer-col h5{font-size:15px;font-weight:400;margin-bottom:12px;padding-bottom:10px;border-bottom:1px solid #777;width:60px}
.contact-line{display:flex;gap:14px;align-items:flex-start;margin-bottom:10px}
</style>
</head>
<body>

<section class="hero">
  <div class="hero-photo" role="img" aria-label="Woman in a knit hat enjoying sunlight in an autumn forest"></div>
  <svg class="abs" style="left:0;top:0" width="1200" height="760" viewBox="0 0 1200 760">
    <path d="M0 720 L0 760 L1200 760 L1200 520 C1000 700 700 745 520 742 C300 738 130 650 0 520 Z" fill="#fff"/>
    <path d="M0 520 C130 650 300 738 520 742 C700 745 1000 700 1200 520" fill="none" stroke="var(--lime)" stroke-width="12"/>
    <path d="M74 303 L56 325 L74 347" fill="none" stroke="#8dc63f" stroke-width="6" stroke-linecap="round"/>
    <path d="M1127 303 L1147 325 L1127 347" fill="none" stroke="var(--taupe)" stroke-width="6" stroke-linecap="round"/>
  </svg>
  <div class="abs hero-welcome">Welcome to</div>
  <div class="abs hero-title">Laanemetsa<br>Haldusgrupp.</div>
  <a class="btn" style="left:579px;top:418px;width:132px;height:45px">Get started</a>
</section>

<header class="site-header">
  <div class="brand" style="left:111px;top:14px"><span class="brand-dot"></span><span>Laanemetsa<br>Haldusgrupp</span></div>
  <nav class="header-nav">
    <span>EN &#8964;</span>
    <span>&#9679; Client Support</span>
    <span class="signup">Sign Up</span>
  </nav>
  <div class="menu"><span></span><span></span><span></span></div>
</header>

<!-- about -->
<h2 class="section-title" style="left:111px;top:836px">About Us</h2>
<p class="copy" style="left:111px;top:904px;width:421px">Lorem ipsum dolor sit amet, consectetur adipiscing elit, sed do eiusmod tempor incididunt ut labore et dolore magna aliqua. Ut enim ad minim veniam, quis nostrud exercitation ullamco laboris nisi ut aliquip ex ea commodo consequat. Duis aute irure dolor in reprehenderit in voluptate velit esse cillum dolore eu fugiat nulla pariatur. Excepteur sint occaecat cupidatat non proident, sunt in culpa qui officia deserunt mollit anim id est laborum.</p>
<a class="btn" style="left:111px;top:1143px;width:131px;height:47px">Learn More</a>
<div class="abs" role="img" aria-label="Hands holding a small patch of green forest" style="left:606px;top:800px;width:430px;height:430px;border-radius:50%;background:radial-gradient(circle at 40% 45%,#8fd23a 0%,#3f9a2a 50%,#1f5e1c 100%)"></div>

<!-- services -->
<section class="services" role="img" aria-label="Misty pine forest background">
  <h2 class="section-title" style="left:372px;top:65px;color:#fff">Environmental Services</h2>
  <div class="service-card" style="left:111px">
    <div class="service-icon"><svg width="40" height="40" viewBox="0 0 40 40" fill="none" stroke="#333" stroke-width="2"><rect x="11" y="14" width="18" height="20" rx="2"/><path d="M8 14h24M16 10h8"/></svg></div>
    <h3>Waste Management</h3>
    <p>Lorem ipsum dolor sit amet, consectetur adipiscing elit, sed do eiusmod tempor incididunt ut labore et dolore magna aliqua.</p>
  </div>
  <div class="service-card active" style="left:445px">
    <div class="service-icon"><svg width="40" height="40" viewBox="0 0 40 40" fill="none" stroke="#333" stroke-width="2"><rect x="14" y="6" width="16" height="20" rx="2"/><circle cx="12" cy="30" r="5"/><circle cx="28" cy="31" r="5"/></svg></div>
    <h3>Environmental Consulting</h3>
    <p>Lorem ipsum dolor sit amet, consectetur adipiscing elit, sed do eiusmod tempor incididunt ut labore et dolore magna aliqua.</p>
  </div>
  <div class="service-card" style="left:778px">
    <div class="service-icon"><svg width="40" height="40" viewBox="0 0 40 40" fill="none" stroke="#333" stroke-width="2"><path d="M20 22V10M20 16c-6 0-8-4-8-8 5 0 8 3 8 8zM20 14c5 0 8-3 8-7-5 0-8 3-8 7zM6 28l8 4h14l6-6"/></svg></div>
    <h3>Environmental Remediation</h3>
    <p>Lorem ipsum dolor sit amet, consectetur adipiscing elit, sed do eiusmod tempor incididunt ut labore et dolore magna aliqua.</p>
  </div>
  <div class="circle-arrow" style="left:50px;top:278px;border:2px solid var(--lime)"><svg width="14" height="14" viewBox="0 0 14 14"><path d="M9 2L4 7l5 5" fill="none" stroke="var(--lime)" stroke-width="2"/></svg></div>
  <div class="circle-arrow" style="left:1108px;top:278px;border:2px solid #fff"><svg width="14" height="14" viewBox="0 0 14 14"><path d="M5 2l5 5-5 5" fill="none" stroke="#fff" stroke-width="2"/></svg></div>
</section>

<!-- company intro -->
<div class="abs" style="left:90px;top:1925px;width:415px;height:388px;border:1.5px solid var(--lime)"></div>
<div class="abs" role="img" aria-label="Hand brushing through tall grass at sunset" style="left:111px;top:1941px;width:415px;height:387px;border-radius:4px;background:radial-gradient(circle at 50% 25%,#f6d37a 0%,#c98a2a 25%,#5e4a1e 60%,#26240f 100%)"></div>
<h2 class="section-title" style="left:603px;top:1944px">Laanemetsa Haldusgrupp</h2>
<p class="copy" style="left:603px;top:2020px;width:485px">Lorem ipsum dolor sit amet, consectetur adipiscing elit, sed do eiusmod tempor incididunt ut labore et dolore magna aliqua. Ut enim ad minim veniam, quis nostrud exercitation ullamco laboris nisi ut aliquip ex ea commodo consequat. Duis aute irure dolor in reprehenderit in voluptate velit esse cillum dolore eu fugiat nulla pariatur. Excepteur sint occaecat cupidatat non proident, sunt in culpa qui officia deserunt mollit anim id est laborum.</p>
<a class="btn" style="left:603px;top:2243px;width:131px;height:46px">Learn More</a>

<!-- reviews -->
<section class="reviews">
  <h2 class="section-title" style="left:452px;top:70px">Client Reviews</h2>
  <div class="review-card" style="left:115px">
    <div class="quote">&#8220;</div><div class="stars">&#9733;&#9733;&#9733;&#9733;&#9733;</div>
    <p>Lorem ipsum dolor sit consectetur adipiscing elit, sed do eius tempor incididunt ut labore et dolor magna aliqua.</p>
    <hr><h4>John Smith</h4><small>Lorem ipsum dolor</small>
  </div>
  <div class="review-card active" style="left:453px">
    <div class="quote">&#8220;</div><div class="stars">&#9733;&#9733;&#9733;&#9733;&#9733;</div>
    <p>Lorem ipsum dolor sit consectetur adipiscing elit, sed do eius tempor incididunt ut labore et dolor magna aliqua.</p>
    <hr><h4>John Smith</h4><small>Lorem ipsum dolor</small>
  </div>
  <div class="review-card" style="left:792px">
    <div class="quote">&#8220;</div><div class="stars">&#9733;&#9733;&#9733;&#9733;&#9733;</div>
    <p>Lorem ipsum dolor sit consectetur adipiscing elit, sed do eius tempor incididunt ut labore et dolor magna aliqua.</p>
    <hr><h4>John Smith</h4><small>Lorem ipsum dolor</small>
  </div>
  <div class="circle-arrow" style="left:57px;top:339px;width:38px;height:38px;border:1.5px solid #888"><svg width="12" height="12" viewBox="0 0 14 14"><path d="M9 2L4 7l5 5" fill="none" stroke="#666" stroke-width="2"/></svg></div>
  <div class="circle-arrow" style="left:1106px;top:339px;width:38px;height:38px;background:var(--taupe)"><svg width="12" height="12" viewBox="0 0 14 14"><path d="M5 2l5 5-5 5" fill="none" stroke="#fff" stroke-width="2"/></svg></div>
</section>

<!-- news -->
<h2 class="section-title" style="left:115px;top:3124px">News and updates</h2>
<a class="btn" style="left:957px;top:3127px;width:131px;height:45px">View All</a>
<article class="news-item" style="left:113px">
  <div class="news-photo" role="img" aria-label="Smiling woman walking in an autumn forest" style="background:linear-gradient(135deg,#6a4a2e,#c89a6a 50%,#8a6e4e)"></div>
  <h4>Lorem ipsum dolor sit amet, consectetur adipiscing elit,</h4><time>06/07/2024</time>
</article>
<article class="news-item" style="left:442px">
  <div class="news-photo" role="img" aria-label="Wooden boardwalk across a misty bog" style="background:linear-gradient(180deg,#cdbfae,#a89478 60%,#6c5a42)"></div>
  <h4>Lorem ipsum dolor sit amet, consectetur adipiscing elit,</h4><time>06/07/2024</time>
</article>
<article class="news-item" style="left:771px">
  <div class="news-photo" role="img" aria-label="Close-up of a frosted pine branch" style="background:radial-gradient(circle at 45% 50%,#e8e4df,#9a8a76 55%,#5e4e3a)"></div>
  <h4>Lorem ipsum dolor sit amet, consectetur adipiscing elit,</h4><time>06/07/2024</time>
</article>

<!-- footer -->
<footer class="site-footer">
  <div class="brand" style="left:111px;top:115px"><span class="brand-dot"></span><span>Laanemetsa<br>Haldusgrupp</span></div>
  <div class="footer-col" style="left:389px">
    <h5>VISIT US</h5>
    <div class="contact-line"><svg width="16" height="20" viewBox="0 0 16 20"><path d="M8 0a7 7 0 0 0-7 7c0 5 7 13 7 13s7-8 7-13a7 7 0 0 0-7-7z" fill="var(--lime)"/><circle cx="8" cy="7" r="2.5" fill="var(--footer)"/></svg><span style="font-size:14px;line-height:24px">Laanemetsa Haldusgrupp<br>Lorem ipsum dolor sit<br>amet, consectetur</span></div>
  </div>
  <div class="footer-col" style="left:638px">
    <h5>CONTACT US</h5>
    <div class="contact-line"><svg width="18" height="18" viewBox="0 0 18 18"><path d="M4 1l3 4-2 2c1 2 3 4 5 5l2-2 4 3-2 3C8 16 2 10 1 4z" fill="var(--lime)"/></svg><span style="font-size:14px">+1 (888) 888 8888</span></div>
    <div class="contact-line"><svg width="18" height="14" viewBox="0 0 18 14"><rect width="18" height="14" rx="1" fill="var(--lime)"/><path d="M1 1l8 6 8-6" fill="none" stroke="var(--footer)" stroke-width="1.5"/></svg><span style="font-size:14px">info@laanemetsahaldus.ee</span></div>
    <div style="width:282px;border-top:1px solid #666;margin-top:8px"></div>
  </div>
  <div class="footer-col" style="left:957px">
    <h5 style="width:70px">QUICK LINKS</h5>
    <div>Terms &amp; Conditions</div><div>Privacy Policy</div><div>About Us</div><div>Support</div>
  </div>
  <div class="abs" style="left:389px;top:240px;font-size:15px">2024 Laanemetsa Haldusgrupp. All Rights Reserved.</div>
</footer>

</body>
</html>
```